Venture 482 - Lumora Book Cover

I am looking for a Lumora book cover for my book about "Venture 482".
The Book is Titled:
Venture 482 Ascended
Shaping Outcomes: Paths To Unlocking Cosmic Truths
Author is Dorian Pell
Here is a book description that may help you understand more about it:
Inspired by the genius of Edwin Marlowe, this comprehensive guide delves into the ancient wisdom and cutting-edge science behind the 482 method, a powerful tool for manifesting your desires. Whether you're seeking personal growth, financial success, or spiritual enlightenment, this book provides advanced techniques and methods to transform your dreams into reality.
Any questions please ask.
Thanks
Owen

```html
<!DOCTYPE html>
<html lang="en">
<head>
<meta charset="utf-8">
<title>Venture 482 – Book Cover</title>
<link rel="stylesheet" href="https://fonts.googleapis.com/css2?family=Cinzel:wght@400&family=Marcellus&display=swap">
<style>
  :root {
    --stage: #d3d3d3;
    --ink: #f8dccb;
    --ink-soft: #efd3c4;
    --night: #1e1a4a;
    --deep-violet: #2a1d5a;
    --cosmic-blue: #2a6fa8;
    --glow-blue: #3f8fc4;
    --ember: #d2552e;
    --ember-soft: #e8894f;
    --plum: #5a2a6a;
    --dusk: #7a3e7e;
  }
  * { margin: 0; padding: 0; box-sizing: border-box; }
  html, body {
    width: 1200px;
    height: 1200px;
    overflow: hidden;
    background: var(--stage);
  }
  .canvas {
    position: relative;
    width: 1200px;
    height: 1200px;
  }
  .cover {
    position: absolute;
    left: 240px;
    top: 25px;
    width: 720px;
    height: 1150px;
    overflow: hidden;
    box-shadow: 2px 3px 6px rgba(0, 0, 0, 0.25);
  }
  .cover-art {
    position: absolute;
    inset: 0;
    background:
      radial-gradient(ellipse 38% 22% at 50% 40%, rgba(63, 143, 196, 0.85), rgba(42, 111, 168, 0) 100%),
      radial-gradient(ellipse 30% 20% at 2% 66%, rgba(232, 137, 79, 0.95), rgba(210, 85, 46, 0.55) 45%, rgba(210, 85, 46, 0) 100%),
      radial-gradient(ellipse 30% 25% at 100% 55%, rgba(210, 85, 46, 0.55), rgba(210, 85, 46, 0) 100%),
      radial-gradient(ellipse 70% 35% at 55% 85%, rgba(122, 62, 126, 0.9), rgba(90, 42, 106, 0) 100%),
      radial-gradient(ellipse 60% 30% at 50% 52%, rgba(42, 111, 168, 0.7), rgba(42, 111, 168, 0) 100%),
      linear-gradient(180deg, var(--night) 0%, var(--deep-violet) 30%, #2f3a7a 50%, var(--plum) 75%, #3a2560 100%);
  }
  .cover-text {
    position: absolute;
    inset: 0;
    color: var(--ink);
    text-align: center;
  }
  .subtitle {
    position: absolute;
    top: 158px;
    left: 0;
    right: 0;
    font-family: "Cinzel", serif;
    font-size: 16px;
    line-height: 22px;
    letter-spacing: 0.5px;
    color: var(--ink-soft);
  }
  .title {
    position: absolute;
    left: 0;
    right: 0;
    font-family: "Marcellus", serif;
    font-weight: 400;
  }
  .title-word {
    top: 340px;
    font-size: 90px;
    line-height: 1;
    letter-spacing: 12px;
    padding-left: 12px;
  }
  .title-number {
    top: 432px;
    font-size: 160px;
    line-height: 1;
    letter-spacing: 2px;
  }
  .author {
    position: absolute;
    top: 1000px;
    left: 0;
    right: 0;
    font-family: "Marcellus", serif;
    font-size: 48px;
    line-height: 1;
    letter-spacing: 5px;
    padding-left: 5px;
  }
</style>
</head>
<body>
  <main class="canvas">
    <section class="cover">
      <div class="cover-art" role="img" aria-label="Cosmic illustration: swirling violet and blue nebula with stars, an orange glow at the left and layered purple mountains below"></div>
      <div class="cover-text">
        <p class="subtitle">SHAPING OUTCOMES<br>PATHS TO UNLOCKING COSMIC TRUTHS</p>
        <h1>
          <span class="title title-word">VENTURE</span>
          <span class="title title-number">482</span>
        </h1>
        <p class="author">DORIAN PELL</p>
      </div>
    </section>
  </main>
</body>
</html>
```